accomplished personal trainer, former elite gymnast from Russia, highly professional and experienced

Established Fitness trainer in California requires a new web site to attract personal clients and build her group exercise classes.

Here is an example of another fitness trainer's site that I really liked the technology:
http://www.tedvorlam.com

Below I have inserted my current web site: www.quelbornfitnesslodi.com
You can use this web site for the principal content, such as my background and qualifications.

Target Market(s)

Anyone who wants to improve their fitness levels and wellness in general. Anyone who needs directions and instruction on how to exercise. I can train anyone from elite athlete to a disabled person.

Industry/Entity Type

Fitness

Coding

Coded - Design and coding required

Number of Pages Required

5+ page

Font styles to use
Sans Serif

Requirements
Must have
• Easy to navigate main info about me, location, services, contact, benefits of using my services.
• Would be great to create unique representation of me as a trainer and a person, using new technologies and new ideas. Make it different from the other websites. Having its own character. Not too complicated and heavy with information, but an eye catching, useful and fun to navigate.
Nice to have
• new technology, easy access to information, the idea of enjoyment of life, lightness about achieving any goal, spiritual wisdom, unique design. I am planning to insert educational videos, advise, maybe jokes. Sign in, shopping cart, logo, should be easy for me to make changes in content.
Should not have
• cliché, outdated technology, too complicated,

```html
<!DOCTYPE html>
<html lang="en">
<head>
<meta charset="utf-8">
<title>Quelborn Fitness Lodi</title>
<link href="https://fonts.googleapis.com/css2?family=Open+Sans:ital,wght@0,400;0,600;0,700;1,400&display=swap" rel="stylesheet">
<style>
:root{
  --pink:#e8409a;
  --ink:#333333;
  --text:#555555;
  --light:#f1f1f1;
  --white:#ffffff;
  --footer:#3a3a3a;
  --footer-deep:#2e2e2e;
  --btn:#3a3a3a;
}
*{box-sizing:border-box;margin:0;padding:0}
html,body{width:1200px;height:4063px;overflow:hidden}
body{font-family:"Open Sans",Arial,sans-serif;color:var(--text);background:var(--white);position:relative}
.section{position:absolute;left:0;width:1200px}
.photo{position:absolute}
.hero{top:0;height:653px}
.hero .photo{inset:0;background:linear-gradient(180deg,#3d6630 0%,#4f7d38 45%,#7fb04f 70%,#8fbf5a 100%)}
.topbar{position:absolute;top:0;left:0;width:1200px;height:90px;display:flex;align-items:center;justify-content:space-between;padding:0 76px}
.brand{font-size:23px;font-weight:700;color:var(--white);white-space:nowrap}
.nav{display:flex;gap:4px;list-style:none}
.nav a{display:block;font-size:13px;font-weight:700;color:var(--white);text-decoration:none;padding:5px 10px;text-transform:uppercase;white-space:nowrap}
.nav a.active{background:var(--pink)}
.hero-arrow{position:absolute;top:310px}
.hero-arrow.left{left:72px}.hero-arrow.right{right:72px}
.heading{font-weight:700;color:var(--ink);text-transform:uppercase;line-height:1.15;letter-spacing:1px}
.heading .accent{color:var(--pink)}
.heading.stack{font-size:42px}
.body-copy{font-size:17px;line-height:1.9;color:var(--text)}
.btn{display:inline-block;background:var(--btn);color:var(--white);font-size:14px;font-weight:700;text-transform:uppercase;text-decoration:none;padding:0 20px;height:48px;line-height:48px;white-space:nowrap;text-align:center;min-width:180px}
.about{top:653px;height:471px}
.about .copy{position:absolute;left:76px;top:45px;width:605px}
.about .body-copy{margin-top:22px}
.about .btn{margin-top:30px}
.about .photo{left:704px;top:57px;width:420px;height:347px;border-radius:8px;background:linear-gradient(135deg,#3e6b32,#6d9a4a 55%,#2f8fc2 85%)}
.banner{top:1124px;height:401px}
.banner .photo{inset:0;background:linear-gradient(90deg,#3b6a2f 0%,#5c8d3f 40%,#e0b49a 60%,#e54f97 80%,#7aa85a 100%)}
.videos{top:1525px;height:398px;background:var(--light)}
.framed{border:4px solid #cfcfcf;border-radius:10px;box-shadow:0 2px 6px rgba(0,0,0,.25)}
.videos .photo{left:76px;top:68px;width:482px;height:276px;background:linear-gradient(135deg,#4a7d35,#7cb04c 60%,#e54f97)}
.play{position:absolute;left:50%;top:50%;transform:translate(-50%,-50%)}
.videos .copy{position:absolute;left:616px;top:55px;width:510px}
.videos .body-copy{margin-top:18px}
.videos .btn{margin-top:26px;min-width:204px}
.services{top:1923px;height:656px}
.service{position:absolute;top:0;width:512px;text-align:center}
.service.left{left:76px}.service.right{left:615px}
.service .heading{font-size:42px;margin-top:38px}
.service .photo{position:relative;width:512px;height:268px;margin-top:22px;border-radius:8px}
.service.left .photo{background:linear-gradient(180deg,#7a9a50,#79b24a 60%,#5f9a3c)}
.service.right .photo{background:linear-gradient(180deg,#9db86a,#6fae45 55%,#57953a)}
.service .body-copy{margin:22px auto 0;width:480px;font-size:16.5px;line-height:1.85}
.service .btn{margin-top:26px}
.group{top:2579px;height:401px}
.group .photo{inset:0;background:linear-gradient(90deg,#2f4f26 0%,#6c8e45 30%,#d8a98a 50%,#b7e04a 70%,#3c5f2e 100%)}
.tips{top:2980px;height:395px}
.tips .copy{position:absolute;left:76px;top:55px;width:540px}
.tips .body-copy{margin-top:14px}
.tips .btn{margin-top:30px}
.tips .photo{left:642px;top:62px;width:485px;height:276px;background:linear-gradient(135deg,#3b6330,#6b9344 45%,#2aa3cf 70%,#2a2a2a)}
.testimonials{top:3375px;height:350px;background:var(--light);text-align:center}
.testimonials .heading{font-size:42px;margin-top:50px}
.quote{font-size:18px;font-style:italic;line-height:1.85;color:var(--text);width:900px;margin:26px auto 0}
.quote-author{font-size:16px;font-weight:700;color:var(--pink);margin-top:16px}
.footer{top:3725px;height:268px;background:var(--footer);color:#cfcfcf}
.footer h4{font-size:18px;font-weight:600;color:var(--white);margin-bottom:14px;white-space:nowrap}
.footer .col{position:absolute;top:45px}
.links{left:76px}
.link-list{list-style:none}
.link-list li{font-size:14px;line-height:28px}
.contact{left:358px;width:390px;font-size:13.5px;line-height:1.9}
.contact .name{color:var(--pink);font-weight:700;margin-top:14px}
.contact .line{display:flex;align-items:center;gap:8px;color:var(--white);white-space:nowrap;font-size:13px}
.newsletter{left:795px;width:330px;font-size:13.5px;line-height:1.9}
.field{margin-top:14px;height:40px;background:var(--white);color:#999;font-size:13px;line-height:40px;padding-left:14px;border:1px solid #ccc}
.signup{position:absolute;right:0;top:160px;background:var(--pink);color:var(--white);font-size:15px;font-weight:700;height:42px;line-height:42px;width:92px;text-align:center}
.baseline{top:3993px;height:70px;background:var(--footer-deep);display:flex;align-items:center;justify-content:space-between;padding:0 76px}
.copyright{font-size:13px;color:#999}
.socials{display:flex;gap:18px}
.socials span{width:19px;height:19px;background:#d8d8d8;border-radius:3px}
</style>
</head>
<body>

<header class="section hero">
  <div class="photo" role="img" aria-label="Trainer stretching in a split pose on a sunny lawn with trees behind"></div>
  <div class="topbar">
    <div class="brand">QUELBORN FITNESS LODI</div>
    <ul class="nav">
      <li><a class="active" href="#">Home</a></li>
      <li><a href="#">Group Classes</a></li>
      <li><a href="#">Personal Training</a></li>
      <li><a href="#">About Quelborn</a></li>
      <li><a href="#">Contact</a></li>
      <li><a href="#">Blog</a></li>
    </ul>
  </div>
  <svg class="hero-arrow left" width="20" height="36" viewBox="0 0 20 36"><path d="M17 3 3 18l14 15" fill="none" stroke="#fff" stroke-width="4" opacity=".8"/></svg>
  <svg class="hero-arrow right" width="20" height="36" viewBox="0 0 20 36"><path d="M3 3l14 15L3 33" fill="none" stroke="#fff" stroke-width="4" opacity=".8"/></svg>
</header>

<section class="section about">
  <div class="copy">
    <h2 class="heading stack">About<br><span class="accent">Quelborn Fitness</span></h2>
    <p class="body-copy">Irina Volkava is the owner of Quelborn Fitness. She was born and raised in Vologda, Russia where she was a competitive gymnast. Irina graduated from Northern State Academy of Sport with a bachelor degree in Kinesiology and Sports Science. For more than 20 years, Irina has worked as choreographer, gymnastics coach, and fitness professional.</p>
    <a class="btn" href="#">Read More</a>
  </div>
  <div class="photo" role="img" aria-label="Trainer in a blue top doing an inverted gymnastic hold outdoors"></div>
</section>

<section class="section banner">
  <div class="photo" role="img" aria-label="Trainer in a pink top doing a side stretch in a park"></div>
</section>

<section class="section videos">
  <div class="photo framed" role="img" aria-label="Video thumbnail of the trainer stretching on grass">
    <svg class="play" width="64" height="64" viewBox="0 0 64 64"><circle cx="32" cy="32" r="28" fill="none" stroke="#fff" stroke-width="4" opacity=".85"/><path d="M25 19v26l21-13z" fill="#fff" opacity=".85"/></svg>
  </div>
  <div class="copy">
    <h2 class="heading stack">Educational<br><span class="accent">Videos</span></h2>
    <p class="body-copy">Lorem ipsum dolor sit amet, consect- etuer adipiscing elit, sed diam nonummy nibh euismod tincidunt ut laoreet dolore magna aliquam erat volutpat.</p>
    <a class="btn" href="#">Watch More Videos</a>
  </div>
</section>

<section class="section services">
  <div class="service left">
    <h2 class="heading">Personal <span class="accent">Training</span></h2>
    <div class="photo" role="img" aria-label="Trainer guiding a client through an exercise ball workout on grass"></div>
    <p class="body-copy">Private sessions will provide you with the motivation you need to reach your goals. As a nationally certified trainer, Irina will make sure you're working out safely and keep the workouts fresh and exciting so you can achieve your goals.</p>
    <a class="btn" href="#">Read More</a>
  </div>
  <div class="service right">
    <h2 class="heading">Group <span class="accent">Classes</span></h2>
    <div class="photo" role="img" aria-label="Group exercise class doing squats together in a park"></div>
    <p class="body-copy">Quelborn Group Exercise classes are designed for people of all fitness levels. Quelborn's group classes take a holistic approach and make sure you work out in a balanced way that feeds your body and spirit.</p>
    <a class="btn" href="#">Read More</a>
  </div>
</section>

<section class="section group">
  <div class="photo" role="img" aria-label="Group of smiling class members in colourful sportswear posing among trees"></div>
</section>

<section class="section tips">
  <div class="copy">
    <h2 class="heading stack">Tips to<br><span class="accent">Members</span></h2>
    <p class="body-copy">Lorem ipsum dolor sit amet, consect- etuer adipiscing elit, sed diam nonummy nibh euismod tincidunt ut laoreet dolore magna aliquam erat volutpat.</p>
    <a class="btn" href="#">Read More</a>
  </div>
  <div class="photo framed" role="img" aria-label="Video thumbnail of a suspension strap workout under trees">
    <svg class="play" width="64" height="64" viewBox="0 0 64 64"><circle cx="32" cy="32" r="28" fill="none" stroke="#fff" stroke-width="4" opacity=".85"/><path d="M25 19v26l21-13z" fill="#fff" opacity=".85"/></svg>
  </div>
</section>

<section class="section testimonials">
  <h2 class="heading">Our <span class="accent">Testimonials</span></h2>
  <p class="quote">"I have known Irina for many years as a fitness trainer and workout class instructor. She is truly one of the very best in the business. Irina is extremely knowledgeable about human physiology and teaching. Her personality is professional, informative, and caring. She would always put "her all" into each of her classes. "</p>
  <p class="quote-author">— Marla Henning</p>
</section>

<footer class="section footer">
  <div class="col links">
    <h4>Quick Links</h4>
    <ul class="link-list">
      <li>Home</li><li>Group Classes</li><li>Personal Training</li><li>About Quelborn</li><li>Contact</li><li>Blog</li>
    </ul>
  </div>
  <div class="col contact">
    <h4>Got a question or comment?</h4>
    <p>We are constantly working to raise the bar on our services. If you have any questions or concerns about your experience, please let us know.</p>
    <p class="name">Irina Volkava</p>
    <p class="line">
      <svg width="13" height="13" viewBox="0 0 24 24"><path d="M6.6 10.8a15 15 0 0 0 6.6 6.6l2.2-2.2a1 1 0 0 1 1-.25 11.4 11.4 0 0 0 3.6.57 1 1 0 0 1 1 1V20a1 1 0 0 1-1 1A17 17 0 0 1 3 4a1 1 0 0 1 1-1h3.5a1 1 0 0 1 1 1c0 1.25.2 2.45.57 3.57a1 1 0 0 1-.25 1z" fill="#fff"/></svg>
      <span>+1 (555) 014-2290</span><span>|</span>
      <svg width="14" height="11" viewBox="0 0 24 18"><rect x="1" y="1" width="22" height="16" fill="#fff"/><path d="M1 1l11 9 11-9" fill="none" stroke="#3a3a3a" stroke-width="2"/></svg>
      <span>irina@quelbornmail.com</span>
    </p>
  </div>
  <div class="col newsletter">
    <h4>SUBSCRIBE NEWSLETTER</h4>
    <p>Sign up with your email address to receive the latest news and updates.</p>
    <div class="field">Enter Email Address</div>
    <div class="signup">SIGN UP</div>
  </div>
</footer>

<div class="section baseline">
  <p class="copyright">Copyright © 2016, Quelborn Fitness Lodi. All Right Reserved</p>
  <div class="socials"><span></span><span></span><span></span><span></span><span></span></div>
</div>

</body>
</html>
```